Website redesign for a Medical Office

We are a physician office in need of a website redesign and a face-lift.
1.Website must work on all platforms including mobile phones and tablets.
2.Website will also include and interactive CONTACT US form and payment gateway for office to collect payment from patients online.
3.Website should have the ability for us to easily edit content without resorting to the services of an IT person.
4. Website content will be collected from the present website www.sunbrookkids.com.
- The type of upgrade we are looking for is more of a corrective work. The major problems with the current website are:
1. Contact Us form not working correctly
2. Credit card/monetrix gateway not working as intended
3. Needing better images/pictures to correctly reflect our business.
4. General enhancement to the overall feel and outlook of the current website.

5. Once a design is selected, website MUST be up and live within TWO WEEKS. The designer able to make this work within the time-frame will get an extra bonus.

Target Market(s)

General public; including patients and their parents.

Industry/Entity Type

Healthcare

Coding

Coded - Design and coding required

Number of Pages Required

5+ page

Font styles to use
Sans Serif

Colors
0492cd
33a6d7
85cae6
cee9f5
cedeed
acd036
cadf82
00a990
f04a50

Requirements
Must have
• 1. Ability for the website to work on all platforms including mobile phones and tablets.
• 2. Include an interactive CONTACT US form
• 3. A payment gateway for office to collect payment from patients online using credit cards and Monetrix.
• 4. Website should have the ability for us to easily edit content without resorting to the services of an IT person.
• 5. Once a design is selected, website MUST be up and live within TWO WEEKS.
• 6. Social network buttons.
• 7. A Vorlund map with office location or geo-tag and directions to office.
Nice to have
• Nice theme, children friendly with a flashy home page and inside pages.
• Attractive design with wow factor

```html
<!DOCTYPE html>
<html lang="en">
<head>
<meta charset="utf-8">
<title>Sunbrook Pediatrics</title>
<link rel="stylesheet" href="https://fonts.googleapis.com/css2?family=Open+Sans:wght@400;600;700&display=swap">
<style>
:root{
  --teal:#00a990;--teal-dark:#008a76;--red:#f04a50;--blue:#0492cd;--green:#acd036;
  --ink:#333;--muted:#666;--soft:#f5f5f5;--footer:#1c1c1c;--footer-deep:#111;--white:#fff;
}
*{box-sizing:border-box;margin:0;padding:0}
html,body{width:1200px;height:3056px;overflow:hidden}
body{font-family:"Open Sans",Arial,sans-serif;color:var(--ink);background:var(--white);font-size:12px;line-height:1.6}
.wrap{width:936px;margin:0 auto;position:relative;height:100%}
/* header */
.site-header{height:115px}
.brand{position:absolute;left:0;top:34px;display:flex;align-items:center;gap:12px}
.brand-mark{width:44px;height:44px;background:var(--blue)}
.brand-name{font-size:25px;font-weight:700;color:var(--blue);line-height:1;letter-spacing:1px}
.header-info{position:absolute;top:38px;display:flex;gap:10px;align-items:flex-start;text-align:right}
.header-info .label{font-size:13px;color:#555}
.header-info .value{font-size:15px;color:var(--red)}
.hours{left:628px}.phone{left:800px}
/* nav */
.main-nav{height:40px;background:var(--teal)}
.main-nav ul{list-style:none;display:flex;height:40px;padding-left:0}
.main-nav li{color:var(--white);font-size:11px;font-weight:600;padding:0 29px;line-height:40px;text-transform:uppercase}
.main-nav li.active{background:var(--teal-dark)}
/* hero */
.hero{height:457px;position:relative;background:linear-gradient(90deg,#c9d8c5 0%,#e8ecdd 40%,#eef0e2 100%)}
.hero-photo{position:absolute;inset:0}
.vision{position:absolute;right:132px;top:90px;width:380px;text-align:right}
.vision h2{font-size:31px;color:var(--red);font-weight:700;line-height:1.2}
.vision p{font-size:11.5px;color:#333;margin-top:6px}
.btn{display:inline-block;color:var(--white);font-size:12px;padding:8px 18px;border-radius:2px}
.btn-red{background:var(--red)}.btn-blue{background:var(--blue)}
.vision .btn{margin-top:14px}
.arrow{position:absolute;top:213px;width:34px;height:34px;border-radius:50%;background:rgba(0,0,0,.18)}
.arrow.prev{left:24px}.arrow.next{right:24px}
.arrow svg{display:block;margin:9px auto}
/* welcome */
.welcome{height:323px;text-align:center;padding-top:78px}
.welcome h1{font-size:33px;color:var(--blue);font-weight:700}
.welcome p{width:936px;margin:14px auto 0;font-size:11.5px;color:#444;line-height:1.75}
.welcome .btn{margin-top:22px}
/* services */
.services{height:333px;background:linear-gradient(180deg,#ece7de,#f9f7f3 50%,#eee9e0);padding-top:66px}
.cards{display:flex;gap:21px}
.card{width:218px;height:212px;background:var(--white);box-shadow:0 1px 4px rgba(0,0,0,.15);text-align:center;padding:30px 16px 0}
.card svg{height:48px}
.card h3{font-size:15px;color:var(--red);font-weight:400;margin-top:10px}
.card p{font-size:9.5px;color:#666;line-height:1.6;margin-top:6px}
/* archives */
.archives{height:572px;padding-top:72px}
.section-title{font-size:31px;font-weight:700;text-align:center;line-height:1.2}
.green{color:var(--green)}
.archives .intro{text-align:center;font-size:11.5px;color:#333;margin:12px auto 0;width:936px;line-height:1.75}
.posts{display:grid;grid-template-columns:494px 442px;row-gap:50px;margin-top:28px}
.post{display:flex;gap:14px}
.thumb{width:160px;height:124px;flex:none}
.post h4{font-size:15px;font-weight:400;color:#222}
.post .meta{font-size:10px;color:#777;margin-top:4px}
.post p{font-size:11px;color:#666;margin-top:10px;line-height:1.65;width:268px}
.post .more{font-size:10px;color:var(--green);margin-top:8px}
/* health center */
.health{height:335px;background:linear-gradient(90deg,#d9d9d9,#efefef 30%,#f4f4f4 70%,#d6d6d6);text-align:center;padding-top:88px}
.health h2{font-size:31px;color:var(--red);font-weight:600}
.tags{display:flex;flex-wrap:wrap;justify-content:center;gap:14px 14px;width:820px;margin:12px auto 0}
.tag{background:var(--red);color:var(--white);font-size:14.5px;padding:8px 18px;border-radius:2px}
/* contact */
.contact{height:605px;background:#f6f6f6;padding-top:72px}
.contact-grid{display:flex;justify-content:space-between;margin-top:34px}
.contact-text{width:470px}
.contact-text h3{font-size:19px;font-weight:400;color:#222;margin-bottom:12px}
.contact-text p{font-size:11.5px;color:#555;line-height:1.8;margin-bottom:16px}
.contact-text ul{list-style:none}
.contact-text li{font-size:11.5px;color:#444;display:flex;gap:14px;align-items:center;margin-bottom:12px}
.contact-text li svg{width:12px;height:12px;flex:none}
.social-row{display:flex;gap:10px;margin-top:18px;align-items:center}
.social-row .sq{width:36px;height:36px;background:#3b5b97}
.social-row .sq.alt{background:#1a7cb5}
.pay{display:flex;gap:6px;margin-left:20px}
.pay span{height:20px;padding:0 6px;font-size:9px;line-height:20px;background:var(--white);border:1px solid #ccc;color:#444}
.map{width:440px;height:340px;background:linear-gradient(135deg,#e9e6df,#f1efea 55%,#e4e0d6);border:6px solid var(--white);box-shadow:0 0 2px rgba(0,0,0,.2)}
/* footer */
.site-footer{height:200px;background:var(--footer);color:#ccc;padding-top:52px}
.foot-grid{display:flex}
.foot-logo{width:68px;height:80px;background:#555;margin:8px 0 0 10px}
.foot-col{font-size:10.5px;line-height:1.75}
.foot-col h5{font-size:12px;font-weight:400;color:var(--white);margin-bottom:8px;letter-spacing:.5px}
.col-contact{margin-left:124px;width:230px}
.col-news{margin-left:56px;width:220px}
.col-follow{margin-left:50px}
.subscribe{display:flex;margin-top:8px}
.subscribe span{width:134px;height:28px;background:var(--white);color:#777;font-size:10px;padding:6px 8px}
.subscribe b{width:52px;height:28px;background:var(--blue);color:var(--white);font-size:10px;font-weight:400;text-align:center;line-height:28px}
.icons{display:flex;gap:8px;margin-top:6px}
.icons i{width:22px;height:22px;background:#ddd;display:block}
.cards-row{display:flex;gap:6px;margin-top:10px}
.cards-row i{width:26px;height:17px;background:#eee;display:block}
.copyright{height:76px;background:var(--footer-deep);color:#bbb;font-size:11px}
.copyright .wrap{display:flex;justify-content:space-between;align-items:center;height:76px}
.seal{width:70px;height:24px;background:#2f5d2f}
</style>
</head>
<body>
<header class="site-header">
  <div class="wrap">
    <div class="brand"><span class="brand-mark"></span><span class="brand-name">SUNBROOK<br>PEDIATRICS</span></div>
    <div class="header-info hours">
      <div><div class="label">Opening Hours</div><div class="value">M-F 8:30AM - 5:30PM</div></div>
      <svg width="30" height="30" viewBox="0 0 30 30"><circle cx="15" cy="15" r="12" fill="none" stroke="#999" stroke-width="2"/><path d="M15 8v7l5 3" fill="none" stroke="#999" stroke-width="2"/></svg>
    </div>
    <div class="header-info phone">
      <div><div class="label">Contact</div><div class="value">(555) 014-2290</div></div>
      <svg width="20" height="32" viewBox="0 0 20 32"><rect x="2" y="2" width="16" height="28" rx="3" fill="none" stroke="#999" stroke-width="2"/><circle cx="10" cy="25" r="1.6" fill="#999"/></svg>
    </div>
  </div>
</header>

<nav class="main-nav">
  <div class="wrap">
    <ul><li class="active">Home</li><li>About Us</li><li>Our Services</li><li>Sunbrook Health Center</li><li>Forms</li><li>Latest News</li><li>Contact Us</li></ul>
  </div>
</nav>

<section class="hero">
  <div class="hero-photo" role="img" aria-label="Photo of two young girls playing with pillows in a bright bedroom with green curtains"></div>
  <div class="vision">
    <h2>OUR VISION</h2>
    <p>To raise a generation of children who are strong and healthy.<br>To create an atmosphere that is friendly and conducive to all<br>families— regardless of age, race, or gender.</p>
    <span class="btn btn-red">Read more</span>
  </div>
  <div class="arrow prev"><svg width="16" height="16" viewBox="0 0 16 16"><path d="M10 3 5 8l5 5" fill="none" stroke="#fff" stroke-width="2"/></svg></div>
  <div class="arrow next"><svg width="16" height="16" viewBox="0 0 16 16"><path d="M6 3l5 5-5 5" fill="none" stroke="#fff" stroke-width="2"/></svg></div>
</section>

<section class="welcome">
  <h1>Welcome to Sunbrook Pediatrics!</h1>
  <p>Sunbrook Pediatrics is a modern pediatric practice dedicated to the health and wellness of children. It is the pediatrician office of choice in Ashford, Georgia. At Sunbrook Pediatrics, you will find a pediatrician and an environment that is warm and compassionate. All of our staff members are knowledgeable, caring, efficient, and ready to serve you.</p>
  <span class="btn btn-blue">Read more</span>
</section>

<section class="services">
  <div class="wrap cards">
    <div class="card">
      <svg viewBox="0 0 52 48" width="52"><path d="M26 44 6 24A11 11 0 0 1 26 10a11 11 0 0 1 20 14Z" fill="#e8403a"/><path d="M8 26h12l4-8 5 14 4-6h11" fill="none" stroke="#fff" stroke-width="2.5"/></svg>
      <h3>General Medical Care</h3>
      <p>Routine Office visits for common ailment, Immunizations, ADHD Evaluation and Treatment, Asthma Care, Allergy Testing, Same day SICK appointments</p>
    </div>
    <div class="card">
      <svg viewBox="0 0 48 48" width="48"><circle cx="24" cy="24" r="20" fill="#f3c9a0"/></svg>
      <h3>Newborn Care</h3>
      <p>Evaluation of the newborn, Infant circumcision</p>
    </div>
    <div class="card">
      <svg viewBox="0 0 40 48" width="40"><path d="M10 4v14a10 10 0 0 0 20 0V4" fill="none" stroke="#555" stroke-width="2.5"/><path d="M20 28v8a7 7 0 0 0 14 0v-6" fill="none" stroke="#2aa38e" stroke-width="2.5"/><circle cx="34" cy="27" r="4" fill="#e8403a"/></svg>
      <h3>Physical Examinations</h3>
      <p>Routine Annual Physicals, Sports Physicals, School and College Physicals, Camp Physicals</p>
    </div>
    <div class="card">
      <svg viewBox="0 0 64 44" width="64"><rect x="4" y="8" width="40" height="26" fill="#f2f2f2" stroke="#999"/><path d="M44 16h10l6 8v10H44Z" fill="#f2f2f2" stroke="#999"/><path d="M20 14h6v6h6v6h-6v6h-6v-6h-6v-6h6Z" fill="#e8403a"/><circle cx="16" cy="36" r="5" fill="#444"/><circle cx="50" cy="36" r="5" fill="#444"/></svg>
      <h3>Emergency Care</h3>
      <p>Management of simple injuries, Strains and sprains, Lacerations, Drainage of simple cysts and abscesses, Removal of foreign bodies and splints</p>
    </div>
  </div>
</section>

<section class="archives">
  <div class="wrap">
    <h2 class="section-title green">From Our Medical Archives</h2>
    <p class="intro">There is nothing more joyful to us as loving parents than that moment when we hold our precious little baby, or babies, in our arms after birth. We should acknowledge them as gifts from God and count ourselves blessed to have them.</p>
    <div class="posts">
      <article class="post">
        <div class="thumb" role="img" aria-label="Cover image with a smiling toddler" style="background:linear-gradient(135deg,#c9a24a,#8a6a3a)"></div>
        <div><h4>Common Childhood Illnesses</h4><div class="meta">14 December, 2016, by Admin</div><p>As they grow and develop, children come in contact with and may sometimes suffer from a variety of common illnesses....</p><div class="more">+ MORE</div></div>
      </article>
      <article class="post">
        <div class="thumb" role="img" aria-label="Photo of a sick child resting in bed with medicine" style="background:linear-gradient(135deg,#e7d6c8,#c9a48c)"></div>
        <div><h4>Common Childhood Illnesses</h4><div class="meta">14 December, 2016, by Admin</div><p>As they grow and develop, children come in contact with and may sometimes suffer from a variety of common illnesses....</p><div class="more">+ MORE</div></div>
      </article>
      <article class="post">
        <div class="thumb" role="img" aria-label="Photo of a pregnant woman in a blue top" style="background:linear-gradient(135deg,#f2f2f2,#7db1d8)"></div>
        <div><h4>Now That You Are Pregnant</h4><div class="meta">14 December, 2016, by Admin</div><p>Congratulations on your pregnancy! A pregnancy that is planned is a thing of joy. There are many changes and adjustments...</p><div class="more">+ MORE</div></div>
      </article>
      <article class="post">
        <div class="thumb" role="img" aria-label="Photo of a mother resting with her newborn baby" style="background:linear-gradient(135deg,#ece8e4,#b9a597)"></div>
        <div><h4>Newborn Care</h4><div class="meta">14 December, 2016, by Admin</div><p>Everyone needs adequate nutrition, and so does your baby. The most natural food for babies is breast milk. Newborn baby and...</p><div class="more">+ MORE</div></div>
      </article>
    </div>
  </div>
</section>

<section class="health" role="img" aria-label="Blurred photo of a clinic interior behind the health center links">
  <h2>Sunbrook Health Center</h2>
  <div class="tags">
    <span class="tag">Well Child Information</span><span class="tag">Immunizations</span><span class="tag">Newborn Care</span><span class="tag">Now That You Are Pregnant</span>
    <span class="tag">Parenting Resources</span><span class="tag">Common Childhood Illnesses</span>
  </div>
</section>

<section class="contact">
  <div class="wrap">
    <h2 class="section-title green">Contact Us</h2>
    <div class="contact-grid">
      <div class="contact-text">
        <h3>About Sunbrook Pediatrics</h3>
        <p>At Sunbrook Pediatrics, you will find a pediatrician and an environment that is warm and compassionate. All of our staff members are knowledgeable, caring, efficient, and ready to serve you.</p>
        <p>The general atmosphere is pleasant, flexible and fun-filled for you and your family to enjoy. It is our pleasure to provide you and your children with our wide range of services.</p>
        <h3>Contact Info</h3>
        <ul>
          <li><svg viewBox="0 0 12 12"><path d="M6 11S2 6.5 2 4.5a4 4 0 0 1 8 0C10 6.5 6 11 6 11Z" fill="#555"/><circle cx="6" cy="4.5" r="1.4" fill="#f6f6f6"/></svg>Sunbrook Pediatrics 22B Willowmere Court Ashford, GA 30100</li>
          <li><svg viewBox="0 0 12 12"><rect x="3" y="1" width="6" height="10" rx="1" fill="none" stroke="#555" stroke-width="1.3"/></svg>(555) 014-2290</li>
          <li><svg viewBox="0 0 12 12"><rect x="1" y="2.5" width="10" height="7" fill="#555"/><path d="M1 3l5 3.5L11 3" fill="none" stroke="#f6f6f6" stroke-width="1"/></svg>info@sunbrookkids.com</li>
        </ul>
        <div class="social-row">
          <span class="sq" aria-label="Social network link"></span><span class="sq alt" aria-label="Social network link"></span>
          <div class="pay"><span>Monetrix</span><span>Cardora</span><span>Kestrapay</span><span>Velta</span></div>
        </div>
      </div>
      <div class="map" role="img" aria-label="Street map showing the office location at 22B Willowmere Court"></div>
    </div>
  </div>
</section>

<footer class="site-footer">
  <div class="wrap foot-grid">
    <div class="foot-logo" aria-label="Sunbrook Pediatrics"></div>
    <div class="foot-col col-contact"><h5>CONTACT US</h5>Address : Sunbrook Pediatrics 22B Willowmere<br>Court Ashford, GA 30100<br>Phone : (555) 014-2290<br>Email : info@sunbrookkids.com</div>
    <div class="foot-col col-news"><h5>SIGN UP FOR NEWSLETTER</h5>Your about us information would fit<br>here nicely.<div class="subscribe"><span>Email address</span><b>Submit</b></div></div>
    <div class="foot-col col-follow"><h5>FOLLOW US OUT THERE</h5><div class="icons"><i></i><i></i><i></i><i></i></div><div class="cards-row"><i></i><i></i><i></i><i></i></div></div>
  </div>
</footer>
<div class="copyright"><div class="wrap"><span>Copyright © 2017. All Rights Reserved</span><span class="seal" aria-label="Security seal"></span></div></div>
</body>
</html>
```